Cleaning service website design

We need a new nice web design(logo will be the same) for a new cleaning service Company:

Informations about Company and logo you can take from flyers in attachments.

This is a cleaning service Company which have simple rules and we would like to show that(in checklist form) on website:

- What we do and that we're Cleaning Green

- Why us?

- How much(our pricing is simple)

Also we would like to communicate with clients by some nice/big pictures on website and the most important thing is our phone number and short/fast Brimtallow.

Also there should be some space for description about our Company.

Generally all information on main page can be short: about us, about service(what we do), last reviews, tips (for example: Tip of the week) and other can be some introduction to subpage where will be more information.

There will be few subpages like: About us, About our service, Photos(Before and after), Reviews , Tips, FAQ, Contact, Looking for a Job? - most of them will be just text so you can project just one example.

```html
<!DOCTYPE html>
<html lang="en">
<head>
<meta charset="utf-8">
<title>Tidy Nest House Cleaning</title>
<link href="https://fonts.googleapis.com/css2?family=Open+Sans:ital,wght@0,300;0,400;0,600;0,700;1,400&family=PT+Sans+Narrow:wght@400;700&display=swap" rel="stylesheet">
<style>
:root{
  --green:#6cb52d;
  --green-dark:#3f8a1a;
  --blue:#1a5fa8;
  --orange:#f47b0c;
  --red:#e8261b;
  --text:#2b2b2b;
  --muted:#777;
  --line:#d7d7d7;
  --footer:#2a2a2a;
  --footer-bottom:#1c1c1c;
}
*{box-sizing:border-box;margin:0;padding:0}
html,body{width:800px;height:1200px;overflow:hidden}
body{position:relative;background:#fff;font-family:"Open Sans",sans-serif;color:var(--text);font-size:9px}
a{color:inherit;text-decoration:none}
.abs{position:absolute}

/* header */
.brand{left:99px;top:18px;width:100px;text-align:center}
.brand-mark{display:flex;align-items:center;gap:5px;justify-content:center;white-space:nowrap}
.brand-dot{width:12px;height:12px;border-radius:50%;background:var(--green);flex:none}
.brand-name{font-size:19px;font-weight:700;color:var(--green-dark)}
.brand-sub{font-size:7px;color:var(--blue);margin-top:12px;font-weight:600;white-space:nowrap}
.call{right:100px;top:9px;text-align:right}
.call small{font-size:8px}
.call small b{font-weight:700}
.call-num{display:flex;align-items:center;justify-content:flex-end;gap:4px;font-size:17px;font-weight:700;margin-top:1px}
.nav{left:270px;top:44px;display:flex;height:45px}
.nav a{font-family:"PT Sans Narrow",sans-serif;font-weight:700;font-size:9px;padding:15px 11px 0;color:#222;text-transform:uppercase;white-space:nowrap}
.nav a.active{background:#f3f3f3;color:var(--green);border-bottom:4px solid var(--green)}
.header-rule{left:0;top:85px;width:800px;height:4px;background:#e9e9e9}

/* hero */
.hero{left:0;top:89px;width:800px;height:336px;background:linear-gradient(100deg,#3c6b2f 0%,#8a5a3a 30%,#c88a5e 50%,#a36a42 70%,#6e9c3b 100%)}
.hero-copy{left:99px;top:122px;color:#fff;text-shadow:0 1px 3px rgba(0,0,0,.5)}
.hero-title{font-size:30px;font-weight:300;line-height:34px;white-space:nowrap}
.hero-title b{font-weight:700}
.hero-sub{font-size:15px;font-weight:600;line-height:22px;white-space:nowrap}
.hero-price{color:var(--red);font-size:26px;font-weight:700;vertical-align:-2px}
.perks{list-style:none;margin-top:8px}
.perks li{display:flex;align-items:center;gap:8px;font-size:10px;height:22.3px;white-space:nowrap}
.badge{left:208px;top:271px;width:46px;height:46px;border-radius:50%;background:#7cc43a;border:2px solid #fff}
.cta{left:99px;top:340px;width:165px;height:39px;border-radius:4px;background:linear-gradient(#ffab2e,#f27a0d);color:#fff;font-size:16px;font-weight:700;display:flex;align-items:center;justify-content:center;gap:8px}

/* cards */
.card{top:450px;height:227px;border:1px solid var(--line);background:#fff;box-shadow:0 6px 6px -4px rgba(0,0,0,.15)}
.card-photo{margin:3px;height:72px}
.card h3{color:var(--green);font-size:12.5px;font-weight:600;text-align:center;margin:8px 0 10px}
.checks{list-style:none;padding:0 14px}
.checks li{display:flex;gap:6px;font-size:8.5px;line-height:12.5px;margin-bottom:6px}
.checks svg{flex:none;margin-top:1px}
.prices{padding:0 22px;font-size:8.5px;line-height:17.5px;white-space:nowrap}
.prices b{color:var(--green-dark);font-weight:400}
.prices p.note{line-height:11.5px;margin-top:4px}
.prices p.note a{color:var(--blue);text-decoration:underline}
.prices p.small{font-size:6.5px;font-style:italic;margin-top:6px}
.estimate h3{font-size:13px;margin-top:12px}
.field{height:19px;border:1px solid #cfcfcf;font-size:6.5px;line-height:8px;color:#999;padding:5px 6px;margin:0 20px 9px;white-space:nowrap;overflow:hidden}
.field-pair{display:flex;gap:8px;margin:0 20px}
.field-pair .field{flex:1;margin:0;padding:5px 4px}
.est-foot{display:flex;justify-content:space-between;align-items:flex-end;margin:16px 20px 0}
.est-foot small{font-size:6.5px;font-weight:700;display:block}
.est-foot strong{color:var(--blue);font-size:12px}
.submit{width:55px;height:17px;background:linear-gradient(#ff9a2e,#e4630a);color:#fff;font-size:7px;font-weight:700;display:flex;align-items:center;justify-content:center}

/* about */
.about{left:99px;top:707px;width:601px;height:95px;border:1px solid var(--line);background:linear-gradient(#fff,#f4f4f4)}
.about-photo{left:0;top:-12px;width:150px;height:106px;background:linear-gradient(90deg,#3a3f48,#c9b496)}
.about h3{left:156px;top:14px;font-family:"PT Sans Narrow",sans-serif;font-weight:400;font-size:20px;color:var(--green-dark)}
.about p{left:156px;top:46px;width:430px;font-size:7.5px;line-height:12.5px}
.about .more{right:13px;top:76px;color:var(--green-dark);font-size:6.5px;font-weight:600}

/* review & tip */
.panel{left:99px;top:827px;width:601px;height:165px;border:1px solid var(--line)}
.panel h3{font-size:12.5px;font-weight:600;color:var(--green)}
.reviewer-photo{left:13px;top:58px;width:92px;height:106px;background:linear-gradient(#e2c9a8,#2b2d33)}
.quote{left:88px;top:36px;width:236px;height:89px;border:1px solid #d4d4d4;border-radius:4px;background:#fff;padding:8px 11px;box-shadow:0 1px 3px rgba(0,0,0,.1)}
.quote .who{font-size:7.5px;font-weight:700}
.quote .who span{font-weight:400;color:var(--muted);margin-left:14px}
.quote p{font-size:7.5px;font-style:italic;color:#555;line-height:12.5px;margin-top:4px}
.quote .meta{border-top:1px dotted #ccc;margin-top:5px;padding-top:4px;font-size:6.5px;display:flex;gap:8px;align-items:center;white-space:nowrap}
.quote .meta .stars{color:var(--red);letter-spacing:-1px}
.quote .meta a{color:var(--blue)}
.btn-more{width:61px;height:16px;background:var(--green-dark);color:#fff;font-size:7px;display:flex;align-items:center;justify-content:center;border-radius:1px}
.divider{left:362px;top:42px;width:1px;height:118px;background:linear-gradient(transparent,#ddd,transparent)}
.tip h4{font-size:9px;font-weight:600;color:var(--blue);text-decoration:underline}
.tip p{font-size:7.5px;line-height:12.5px;margin-top:7px;width:200px}

/* footer */
.footer{left:0;top:1017px;width:800px;height:156px;background:var(--footer);color:#fff}
.fcol h4{font-size:10.5px;font-weight:600;margin-bottom:8px;white-space:nowrap}
.fcol a{display:block;font-size:7.5px;line-height:15.7px}
.fcol p{font-size:7.5px}
.newsletter{display:flex;gap:4px;margin-top:8px}
.newsletter .email{width:207px;height:26px;background:#fff;color:#222;font-size:7.5px;padding:8px 10px;border-radius:2px}
.newsletter .go{width:28px;height:26px;background:linear-gradient(#ffb43a,#f07a0c);font-size:8px;font-weight:700;display:flex;align-items:center;justify-content:center;border-radius:2px}
.socials{display:flex;gap:7px}
.socials span{width:15px;height:15px;border-radius:2px}
.foot-brand{display:flex;align-items:center;gap:5px;font-size:15px;font-weight:700;color:var(--green);white-space:nowrap}
.bottom{left:0;top:1173px;width:800px;height:27px;background:var(--footer-bottom);color:#555;font-size:7px;padding:9px 99px}
</style>
</head>
<body>

<!-- header -->
<div class="abs brand">
  <div class="brand-mark"><span class="brand-dot"></span><span class="brand-name">Tidy Nest</span></div>
  <div class="brand-sub">House Cleaning</div>
</div>
<div class="abs call">
  <small><b>Call Us</b> to arrange your cleaning on</small>
  <div class="call-num">
    <svg width="12" height="14" viewBox="0 0 12 14"><path d="M3 1 L5 4 L3.5 5.5 Q4.5 8.5 7 10 L8.5 8.5 L11 11 L9 13 Q2 11 1 3 Z" fill="var(--blue)"/></svg>
    555-014-2290
  </div>
</div>
<nav class="abs nav">
  <a class="active" href="#">Home</a><a href="#">About us</a><a href="#">Our services</a><a href="#">Photos</a><a href="#">Reviews</a><a href="#">Tips</a><a href="#">Careers</a><a href="#">FAQ</a><a href="#">Contact</a>
</nav>
<div class="abs header-rule"></div>

<!-- hero -->
<div class="abs hero" role="img" aria-label="Smiling family of four close together outdoors"></div>
<div class="abs hero-copy">
  <div class="hero-title">SIMPLIFY <b>YOUR LIFE</b></div>
  <div class="hero-sub">and some there House Cleaning from <span class="hero-price">$79</span></div>
  <ul class="perks">
    <li><svg width="14" height="14" viewBox="0 0 14 14"><path d="M2 13 Q1 4 13 1 Q12 12 2 13Z" fill="#5fb82a"/></svg>Locally Owned &amp; Operated</li>
    <li><svg width="14" height="14" viewBox="0 0 14 14"><path d="M2 13 Q1 4 13 1 Q12 12 2 13Z" fill="#5fb82a"/></svg>Reliable &amp; Affordable</li>
    <li><svg width="14" height="14" viewBox="0 0 14 14"><path d="M2 13 Q1 4 13 1 Q12 12 2 13Z" fill="#5fb82a"/></svg>All Supplies Provided</li>
    <li><svg width="14" height="14" viewBox="0 0 14 14"><path d="M2 13 Q1 4 13 1 Q12 12 2 13Z" fill="#5fb82a"/></svg>No Contracts</li>
    <li><svg width="14" height="14" viewBox="0 0 14 14"><path d="M2 13 Q1 4 13 1 Q12 12 2 13Z" fill="#5fb82a"/></svg>Pet Friendly</li>
    <li><svg width="14" height="14" viewBox="0 0 14 14"><path d="M2 13 Q1 4 13 1 Q12 12 2 13Z" fill="#5fb82a"/></svg>Green Cleaning</li>
  </ul>
</div>
<div class="abs badge"></div>
<a class="abs cta" href="#">GET STARTED
  <svg width="18" height="16" viewBox="0 0 18 16"><path d="M0 5 H9 V0 L18 8 L9 16 V11 H0 Z" fill="#fff"/></svg>
</a>

<!-- cards -->
<section class="abs card" style="left:99px;width:191px">
  <div class="card-photo" role="img" aria-label="Family with their dog relaxing on a sofa" style="background:linear-gradient(90deg,#c4a57a,#efe3cf,#b98e63)"></div>
  <h3>What do we clean?</h3>
  <ul class="checks">
    <li><svg width="11" height="11" viewBox="0 0 11 11"><rect x=".5" y="1.5" width="9" height="9" fill="none" stroke="#666"/><path d="M2.5 5 L5 8 L10.5 1" fill="none" stroke="var(--green-dark)" stroke-width="1.6"/></svg>Thoroughly clean your bathrooms, kitchen, bedrooms and living areas</li>
    <li><svg width="11" height="11" viewBox="0 0 11 11"><rect x=".5" y="1.5" width="9" height="9" fill="none" stroke="#666"/><path d="M2.5 5 L5 8 L10.5 1" fill="none" stroke="var(--green-dark)" stroke-width="1.6"/></svg>Mop or vacuum your floors</li>
    <li><svg width="11" height="11" viewBox="0 0 11 11"><rect x=".5" y="1.5" width="9" height="9" fill="none" stroke="#666"/><path d="M2.5 5 L5 8 L10.5 1" fill="none" stroke="var(--green-dark)" stroke-width="1.6"/></svg>Dust surfaces</li>
    <li><svg width="11" height="11" viewBox="0 0 11 11"><rect x=".5" y="1.5" width="9" height="9" fill="none" stroke="#666"/><path d="M2.5 5 L5 8 L10.5 1" fill="none" stroke="var(--green-dark)" stroke-width="1.6"/></svg>Collect garbage</li>
    <li><svg width="11" height="11" viewBox="0 0 11 11"><rect x=".5" y="1.5" width="9" height="9" fill="none" stroke="#666"/><path d="M2.5 5 L5 8 L10.5 1" fill="none" stroke="var(--green-dark)" stroke-width="1.6"/></svg>Make beds</li>
  </ul>
</section>

<section class="abs card" style="left:303px;width:191px">
  <div class="card-photo" role="img" aria-label="Family gathered around a laptop" style="background:linear-gradient(90deg,#d9c3a3,#f3ede4,#9fb4c6)"></div>
  <h3>Pricing is..simple</h3>
  <div class="prices">
    <div><b>$79</b> for homes less than 1000 sq ft</div>
    <div><b>$89</b> for homes 1000-1800 sq ft</div>
    <div><b>$99</b> for homes 1800-2600 sq ft</div>
    <p class="note">If your home is larger than 2600 sq ft<br>please <a href="#">call for a quote</a></p>
    <p class="small">*rates are for regular service*</p>
  </div>
</section>

<section class="abs card estimate" style="left:507px;width:192px">
  <h3 style="color:var(--green);text-align:center;font-weight:600">Quick Free Estimate</h3>
  <div class="field" style="margin-top:4px">Name</div>
  <div class="field">E-mail</div>
  <div class="field">Postal Code</div>
  <div class="field">Phone</div>
  <div class="field-pair"><div class="field">No. of Bathrooms</div><div class="field">No. of Bedrooms</div></div>
  <div class="est-foot">
    <div><small>CALL US TODAY</small><strong>555-014-2290</strong></div>
    <div class="submit">SUBMIT</div>
  </div>
</section>

<!-- about -->
<section class="abs about">
  <div class="abs about-photo" role="img" aria-label="Company owners, a man and a woman, in winter jackets"></div>
  <h3 class="abs">About TidyNest.com</h3>
  <p class="abs">It’s about caring, not just cleaning. Having personally experienced the struggles of finding quality maid service for our home, we want to make it simpler for families in the Brookfield area. Our goal is to provide caring, consistent and reliable house cleaning to every customer we serve.</p>
  <a class="abs more" href="#">READ MORE...</a>
</section>

<!-- review & tip -->
<section class="abs panel">
  <h3 class="abs" style="left:18px;top:14px">Featured Review</h3>
  <div class="abs reviewer-photo" role="img" aria-label="Smiling reviewer in a business jacket"></div>
  <div class="abs quote">
    <div class="who">Dana Morrow, Brookfield <span>1 review</span></div>
    <p>I had to move out of a rental property and didn’t want to hassle with the cleaning, so I called Tidy Nest whom quoted me over the phone and did a brilliant job.</p>
    <div class="meta"><span class="stars">★★★★★</span><span>09/07/2013</span><a href="#">COMMENT</a><a href="#">REPORT</a><a href="#">Share</a><span>HELPFUL?</span></div>
  </div>
  <a class="abs btn-more" href="#" style="left:261px;top:136px">View more &gt;</a>

  <div class="abs divider"></div>

  <div class="abs tip" style="left:384px;top:14px">
    <h3>Tip of the Week</h3>
    <h4 style="margin-top:15px">Cleaning up after your dog or cat</h4>
    <p>For millions of dog and cat owners, Fido and Fluffy aren’t just pets – they’re part of the family. But as much as we love our four-legged friends, they sure can .....</p>
  </div>
  <a class="abs btn-more" href="#" style="left:513px;top:136px">View more &gt;</a>
</section>

<!-- footer -->
<footer class="abs footer">
  <div class="abs fcol" style="left:99px;top:26px">
    <h4>Quick Links</h4>
    <a href="#">Home</a><a href="#">About Us</a><a href="#">Our Service</a><a href="#">Photos</a><a href="#">Contact</a>
  </div>
  <div class="abs fcol" style="left:220px;top:26px">
    <h4>Useful Links</h4>
    <a href="#">Terms of use</a><a href="#">Privacy Policy</a><a href="#">Help Center</a><a href="#">Community</a><a href="#">Login Area</a>
  </div>
  <div class="abs fcol" style="left:327px;top:26px">
    <h4>Join Our Community</h4>
    <a href="#">Friendloop</a><a href="#">Chirpline</a><a href="#">Workweave</a>
  </div>
  <div class="abs fcol" style="left:463px;top:26px">
    <h4>SignUp For Our Monthly Newsletter</h4>
    <p>Subscribe our newsletter &amp; get the latest news &amp; updates</p>
    <div class="newsletter"><div class="email">Email Address</div><div class="go">GO</div></div>
  </div>
  <div class="abs socials" style="left:463px;top:114px">
    <span style="background:#3b5ca8"></span><span style="background:#3fa9e0"></span><span style="background:#f39a1c"></span>
  </div>
  <div class="abs foot-brand" style="left:632px;top:112px"><span class="brand-dot"></span>Tidy Nest</div>
</footer>
<div class="abs bottom">© 2013 by, Tidy Nest. All Rights Reserved.</div>

</body>
</html>
```